Road Construction Company needs business cards

We would like a new business card designed for our business.

We're a road construction company based in Qld, Australia.

Can the business card please have the following information on it.

Name: Warren Halbeck
Position: General Manager
Phone: 0472 915 348
Email: Warren.halbeck@tovrin.com.au
Address: 87 Marrow Ave, Pendlebay, QLD, 4023
Website: www.tovrin.com.au

Visually we'd like the card to be professional and simple.

Attached is our logo.

Our website is www.tovrin.com.au

Target Market(s)

Men aged 25-60

Contact Information for Business Card

As listed in project description

Font styles to use
Serif

Requirements
Must have
• Large logo on back of card

```html
<!DOCTYPE html>
<html lang="en">
<head>
<meta charset="utf-8">
<title>Tovrin – Business Card</title>
<link href="https://fonts.googleapis.com/css2?family=Didact+Gothic&family=Open+Sans:wght@700&display=swap" rel="stylesheet">
<style>
  :root {
    --page: #e6e8eb;
    --card: #ffffff;
    --band: #2f9ccf;
    --navy: #1d4e9b;
    --crease: #cdd2d8;
    --ink-light: #ffffff;
  }
  * { margin: 0; padding: 0; box-sizing: border-box; }
  html, body { width: 1200px; height: 900px; overflow: hidden; background: var(--page); }
  .canvas { position: relative; width: 1200px; height: 900px; }
  .card {
    position: absolute; left: 250px; width: 700px; height: 400px;
    background: linear-gradient(135deg, #ffffff 0%, #f3f4f6 100%);
    box-shadow: 0 6px 18px rgba(0,0,0,0.18);
    overflow: hidden;
  }
  .card--back { top: 40px; }
  .card--front { top: 470px; }
  .card__shape { position: absolute; inset: 0; width: 700px; height: 400px; }
  .wordmark {
    position: absolute; right: 62px;
    font-family: "Open Sans", sans-serif; font-weight: 700;
    font-size: 60px; letter-spacing: 4px; color: var(--navy); line-height: 1;
  }
  .card--back .wordmark { top: 205px; }
  .card--front .wordmark { top: 48px; }
  .contact { position: absolute; left: 96px; top: 78px; font-family: "Didact Gothic", sans-serif; }
  .contact__name {
    font-family: "Open Sans", sans-serif; font-weight: 700;
    font-size: 21px; color: var(--navy); text-transform: uppercase; line-height: 1.1;
  }
  .contact__role { font-size: 16px; color: var(--ink-light); margin-left: 12px; }
  .contact__row { display: flex; align-items: flex-start; gap: 8px; color: var(--ink-light); font-size: 17px; line-height: 1.3; }
  .contact__row svg { width: 16px; height: 16px; flex: none; margin-top: 3px; fill: var(--navy); }
  .contact__address { margin: 58px 0 0 24px; }
  .contact__list { margin: 46px 0 0 60px; }
</style>
</head>
<body>
<main class="canvas">
  <section class="card card--back" aria-label="Card back">
    <div class="wordmark">TOVRIN</div>
  </section>

  <section class="card card--front" aria-label="Card front">
    <svg class="card__shape" viewBox="0 0 700 400" aria-hidden="true">
      <line x1="276" y1="0" x2="494" y2="400" stroke="var(--crease)" stroke-width="6"/>
      <polygon fill="var(--band)" points="63,0 273,0 490,400 252,400 200,334 132,334 90,400 0,400 0,108"/>
      <polyline fill="none" stroke="var(--crease)" stroke-width="3" points="90,400 132,334 200,334"/>
    </svg>
    <div class="wordmark">TOVRIN</div>
    <div class="contact">
      <p class="contact__name">Warren Halbeck</p>
      <p class="contact__role">General Manager</p>
      <div class="contact__row contact__address">
        <svg viewBox="0 0 16 16"><path d="M8 0a5.5 5.5 0 0 0-5.5 5.5C2.5 10 8 16 8 16s5.5-6 5.5-10.5A5.5 5.5 0 0 0 8 0zm0 8a2.5 2.5 0 1 1 0-5 2.5 2.5 0 0 1 0 5z"/></svg>
        <p>87 Marrow Ave<br>Pendlebay, QLD, 4023</p>
      </div>
      <div class="contact__list">
        <div class="contact__row">
          <svg viewBox="0 0 16 16"><path d="M3.6 0.5l2.4 2.9-1.5 2.1c.9 2 2.4 3.6 4.4 4.6l2.1-1.4 2.9 2.4-1.5 3C7 13.8 2 8.8 0.6 2z"/></svg>
          <p>0472 915 348</p>
        </div>
        <div class="contact__row">
          <svg viewBox="0 0 16 16"><path d="M8 0a8 8 0 1 0 0 16A8 8 0 0 0 8 0zm0 1.6c.9 0 1.9 1.9 2.2 4.6H5.8C6.1 3.5 7.1 1.6 8 1.6zM1.7 7.2h2.6c0 .5 0 1.1.1 1.6H1.7a6.4 6.4 0 0 1 0-1.6zm4.1 2.6h4.4C9.9 12.5 8.9 14.4 8 14.4s-1.9-1.9-2.2-4.6zm5.9-1c0-.5.1-1.1.1-1.6h2.6a6.4 6.4 0 0 1 0 1.6z"/></svg>
          <p>www.tovrin.com.au</p>
        </div>
        <div class="contact__row">
          <svg viewBox="0 0 16 16"><path d="M0 3h16v10H0zm1.5 1.5L8 9l6.5-4.5v-.1h-13z"/></svg>
          <p>Warren.halbeck@tovrin.com.au</p>
        </div>
      </div>
    </div>
  </section>
</main>
</body>
</html>
```